Real Estate Brokerage Stationery Designs

I am looking to have presentation folders with business card slots on both sides along with pockets on both sides. I've attached logos, website colors along with current business card designs.

I am looking for envelope designs both big and small. Possibly new business card designs, notepad templates for big and small notepads. Letterhead designs. Pop socket designs. Realtors name badge designs.

www.brightholdrealty.example

```html
<!DOCTYPE html>
<html lang="en">
<head>
<meta charset="utf-8">
<title>Brighthold Realty Stationery</title>
<link href="https://fonts.googleapis.com/css2?family=Open+Sans:wght@400;600&family=Tinos&display=swap" rel="stylesheet">
<style>
:root{
  --backdrop:#aaa9a9;
  --paper:#f4f4f4;
  --paper-shade:#e2e2e2;
  --brand-blue:#0056a6;
  --ink:#3a3a3a;
  --ink-soft:#555;
  --white:#fff;
}
*{margin:0;padding:0;box-sizing:border-box}
html,body{width:1200px;height:871px;overflow:hidden;background:var(--backdrop)}
.canvas{position:relative;width:1200px;height:871px}
.sheet{position:absolute;background:linear-gradient(90deg,var(--paper),var(--paper-shade));box-shadow:0 1px 3px rgba(0,0,0,.25)}
.brand-name{font-family:"Open Sans",sans-serif;font-weight:600;color:var(--brand-blue);display:flex;align-items:center;gap:6px;white-space:nowrap}
.brand-name .mark{width:12px;height:12px;background:var(--brand-blue);flex:none}
/* envelope front */
.envelope-front{left:54px;top:216px;width:560px;height:254px}
.envelope-front .accent-bar{position:absolute;left:0;top:47px;width:9px;height:74px;background:var(--brand-blue)}
.envelope-front .brand-name{position:absolute;left:32px;top:96px;font-size:16px}
.envelope-front .return-address{position:absolute;left:30px;top:124px;width:104px;text-align:center;font:7px/1.35 "Open Sans",sans-serif;color:var(--ink-soft)}
/* envelope back */
.envelope-back{left:54px;top:500px;width:560px;height:254px}
.envelope-back .flap{position:absolute;left:0;top:0;width:560px;height:94px}
.envelope-back .flap-name{position:absolute;left:0;top:34px;width:560px;justify-content:center;color:var(--white);font-size:16px}
.envelope-back .flap-name .mark{background:var(--white)}
/* letterhead */
.letterhead{left:638px;top:57px;width:522px;height:734px}
.letterhead .brand-name{position:absolute;left:46px;top:128px;font-size:17px}
.contact-box{position:absolute;left:365px;top:40px;width:157px;height:81px;background:var(--brand-blue);color:var(--white);font:7px/1.4 "Open Sans",sans-serif;padding:3px 0 0 10px}
.contact-box .address{margin-bottom:6px}
.contact-box ul{list-style:none}
.contact-box li{display:flex;align-items:center;gap:6px;line-height:10.4px}
.contact-box svg{width:7px;height:7px;flex:none}
.letter{position:absolute;left:48px;top:180px;width:432px;font-family:"Tinos",serif;color:var(--ink-soft)}
.letter .date{font-size:9.6px;margin-bottom:26px}
.letter .recipient{font-size:9.6px;line-height:12px;margin-bottom:20px}
.letter p.body{font-size:7.6px;line-height:12px;text-align:justify;margin-bottom:12px}
.signature-area{position:absolute;left:50px;top:584px;width:108px;height:44px;background:linear-gradient(90deg,rgba(90,90,90,.15),rgba(90,90,90,.05))}
</style>
</head>
<body>
<div class="canvas">

  <section class="sheet envelope-front">
    <div class="accent-bar"></div>
    <div class="brand-name"><span class="mark"></span>Brighthold Realty</div>
    <p class="return-address">2750 Harbor View Way, Suite 310,<br>Lakemont, FL 33900</p>
  </section>

  <section class="sheet envelope-back">
    <svg class="flap" viewBox="0 0 560 94" aria-hidden="true">
      <path d="M0 0H560L547 64Q541 94 510 94H50Q19 94 13 64Z" fill="var(--brand-blue)"/>
    </svg>
    <div class="brand-name flap-name"><span class="mark"></span>Brighthold Realty</div>
  </section>

  <section class="sheet letterhead">
    <div class="brand-name"><span class="mark"></span>Brighthold Realty</div>
    <div class="contact-box">
      <p class="address">2750 Harbor View Way, Suite 310,<br>Lakemont, FL 33900</p>
      <ul>
        <li><svg viewBox="0 0 10 10"><path d="M1 3Q5 0 9 3V5H7V4H3V5H1ZM2 6H8V9H2Z" fill="#fff"/></svg>555-210-4410</li>
        <li><svg viewBox="0 0 10 10"><rect x="2.5" y="0.5" width="5" height="9" rx="1" fill="none" stroke="#fff"/></svg>555-210-4422</li>
        <li><svg viewBox="0 0 10 10"><rect x="1" y="4" width="8" height="5" fill="#fff"/><rect x="3" y="1" width="4" height="3" fill="#fff"/></svg>555-210-4435</li>
        <li><svg viewBox="0 0 10 10"><rect x="0.5" y="2" width="9" height="6" fill="#fff"/></svg>office@brightholdrealty.example</li>
        <li><svg viewBox="0 0 10 10"><circle cx="5" cy="5" r="4.5" fill="#fff"/></svg>www.brightholdrealty.example</li>
      </ul>
    </div>
    <div class="letter">
      <p class="date">Port Alden, Ocober 12,2015</p>
      <p class="recipient">Sr.<br>MARCO REYES<br>Web Master<br>City</p>
      <p class="body">Contrary to popular belief, Lorem Ipsum is not simply random text. It has roots in a piece of classical Latin literature from 45 BC, making it over 2000 years old. Edwin Harlow, a Latin professor at Westbrook College in Vermont, looked up one of the more obscure Latin words, consectetur, from a Lorem Ipsum passage, and going through the cites of the word in classical literature,</p>
      <p class="body">discovered the undoubtable source. Lorem Ipsum comes from sections 1.10.32 and 1.10.33 of "de Finibus Bonorum et Malorum" (The Extremes of Good and Evil) by an ancient author, written in 45 BC. This book is a treatise on the theory of ethics, very popular during the Renaissance. The first line of Lorem Ipsum, "Lorem ipsum dolor sit amet..", comes from a line in section 1.10.32.</p>
      <p class="body">The standard chunk of Lorem Ipsum used since the 1500s is reproduced below for those interested. Sections 1.10.32 and 1.10.33 from "de Finibus Bonorum et Malorum" by the same author are also reproduced in their exact original form, accompanied by English versions from the 1914 translation by T. Marlowe.</p>
      <p class="body">There are many variations of passages of Lorem Ipsum available, but the majority have suffered alteration in some form, by injected humour, or randomised words which don't look even slightly believable. If you are going to use a passage of Lorem Ipsum, you need to be sure there isn't anything embarrassing hidden in the middle of text.</p>
    </div>
    <div class="signature-area" role="img" aria-label="Handwritten signature of the sender"></div>
  </section>

</div>
</body>
</html>
```